Brightfield Ventures Inc. Letterhead

Creation of attractive and eye catching letterhead for a business start-up for the construction industry. Letterhead must relate to construction, but avoid standard hammer and tools in the design.

I forgot to add some details, sorry about that. Some pertinent info: Ph: 916-555-0187 brightfieldventures.example 448 Willowmere Ave, Ste 210 Folsom, CA 95999 info@brightfieldventures.example not sure if slogan should be in there" “Connecting construction professionals to create a purpose driven industry.” must be able to be used in word. Thanks!

```html
<!DOCTYPE html>
<html lang="en">
<head>
<meta charset="utf-8">
<title>Brightfield Ventures Inc. Letterhead</title>
<link href="https://fonts.googleapis.com/css2?family=Lato:wght@400;700&family=Courgette&display=swap" rel="stylesheet">
<style>
  :root {
    --navy: #1b2155;
    --red: #c11f2a;
    --text: #444548;
    --paper: #ffffff;
    --stage: #e9e9ea;
  }
  * { margin: 0; padding: 0; box-sizing: border-box; }
  html, body { width: 906px; height: 1200px; overflow: hidden; background: var(--stage); }
  .letterhead {
    position: relative;
    width: 906px;
    height: 1200px;
    background: var(--paper);
    font-family: "Lato", sans-serif;
    color: var(--text);
  }
  .header-band { position: absolute; top: 0; left: 0; width: 906px; height: 130px; }
  .contact-list {
    position: absolute;
    top: 22px;
    left: 632px;
    list-style: none;
    color: #fff;
    font-size: 13px;
    line-height: 21px;
  }
  .contact-list li { display: flex; align-items: center; gap: 5px; }
  .contact-list svg { width: 10px; height: 10px; flex: none; }
  .brand {
    position: absolute;
    top: 150px;
    left: 64px;
    display: flex;
    align-items: center;
    gap: 10px;
  }
  .brand-square { width: 14px; height: 14px; background: var(--red); }
  .brand-name {
    font-weight: 700;
    font-size: 21px;
    letter-spacing: 0.5px;
    color: var(--navy);
  }
  .letter-body {
    position: absolute;
    top: 332px;
    left: 64px;
    width: 778px;
  }
  .salutation { font-weight: 700; font-size: 16px; color: var(--navy); margin-bottom: 18px; }
  .letter-body p.para {
    font-size: 16.5px;
    line-height: 26.5px;
    text-align: justify;
    margin-bottom: 20px;
  }
  .closing { font-size: 19px; color: #222; margin-top: 28px; }
  .signature {
    font-family: "Courgette", cursive;
    font-size: 30px;
    color: var(--navy);
    margin-top: 4px;
  }
  .footer-address {
    position: absolute;
    top: 1140px;
    left: 0;
    width: 906px;
    text-align: center;
    font-size: 14px;
    color: #333;
  }
  .footer-bar { position: absolute; bottom: 0; left: 0; width: 906px; height: 19px; background: var(--red); }
</style>
</head>
<body>
<main class="letterhead">
  <svg class="header-band" viewBox="0 0 906 130" aria-hidden="true">
    <path fill="var(--red)" d="M0 76 C 90 44, 210 30, 330 34 C 470 40, 560 100, 680 114 C 770 122, 860 108, 906 94 V 84 C 860 100, 770 112, 680 104 C 560 92, 470 40, 330 30 C 200 22, 80 35, 0 62 Z"/>
    <path fill="var(--navy)" d="M0 0 H906 V84 C 860 100, 770 112, 680 104 C 560 92, 470 40, 330 30 C 200 22, 80 35, 0 62 Z"/>
  </svg>

  <ul class="contact-list">
    <li>
      <svg viewBox="0 0 10 10"><path fill="#fff" d="M2 0.5 L3.8 2.6 L2.9 3.6 C3.5 5 4.9 6.4 6.4 7.1 L7.4 6.2 L9.5 8 L8.2 9.5 C4.5 9 1 5.5 0.5 1.8 Z"/></svg>
      916-555-0187
    </li>
    <li>
      <svg viewBox="0 0 10 10"><rect x="0.5" y="2" width="9" height="6.5" fill="#fff"/><path d="M0.5 2 L5 5.5 L9.5 2" stroke="var(--navy)" fill="none" stroke-width="0.9"/></svg>
      info@brightfieldventures.example
    </li>
    <li>
      <svg viewBox="0 0 10 10"><circle cx="5" cy="5" r="4.3" fill="none" stroke="#fff"/><path d="M0.7 5 H9.3 M5 0.7 C2.5 3 2.5 7 5 9.3 M5 0.7 C7.5 3 7.5 7 5 9.3" stroke="#fff" fill="none" stroke-width="0.8"/></svg>
      www.brightfieldventures.example
    </li>
  </ul>

  <div class="brand">
    <span class="brand-square"></span>
    <span class="brand-name">Brightfield Ventures Inc.</span>
  </div>

  <section class="letter-body">
    <p class="salutation">Dear Mr. Lorem,</p>
    <p class="para">Lorem ipsum dolor sit amet, consectetuer adipiscing elit, sed diam nonummy nibh euismod tincidunt ut laoreet dolore magna aliquam erat volutpat. Ut wisi enim ad minim veniam, quis nostrud exerci tation ullamcorper suscipit lobortis nisl ut aliquip ex ea commodo consequat. Duis autem vel eum iriure dolor in hendiusto odio dignissim qui blandit praesent luptatum zzril delenit augue duis dolore te feugait nulla facilisi.</p>
    <p class="para">Lorem ipsum dolor sit amet, consectetuer adipiscing elit, sed diam nonummy nibh euismod tincidunt ut laoreet dolore magna aliquam erat volutpat. Ut wisi enim ad minim veniam, quis nostrud exerci tation ullamcorper suscipit lobortis nisl ut aliquip ex ea commodo consequat. Duis autem vel eum iriure dolor in hendiusto odio dignissim qui blandit praesent luptatum zzril delenit augue duis dolore te feugait nulla facilisi.</p>
    <p class="para">Lorem ipsum dolor sit amet, consectetuer adipiscing elit, sed diam nonummy nibh euismod tincidunt ut laoreet dolore magna aliquam erat volutpat. Ut wisi enim ad minim veniam, quis nostrud exerci tation ullamcorper suscipit lobortis nisl ut aliquip ex ea commodo consequat. Duis autem vel eum iriure dolor in hendiusto odio dignissim qui blandit praesent luptatum zzril delenit augue duis dolore te feugait nulla facilisi.</p>
    <p class="closing">Sincerely Your,</p>
    <p class="signature">Your Name</p>
  </section>

  <p class="footer-address">448 Willowmere Ave, Ste 210, Folsom, CA 95999</p>
  <div class="footer-bar"></div>
</main>
</body>
</html>
```